Business Card Design Project

Business Card
We are rebranding with a new logo
Industry/Entity Type
Business
Contact Information for Business Card
Dennis Morvale +61 487215963 dennis@quorv.com.au P.O. Box 872 Fernlow QLD 4309
Requirements
Must have
- Logo

```html
<!DOCTYPE html>
<html lang="en">
<head>
<meta charset="utf-8">
<title>Quorv International – Business Card</title>
<link rel="stylesheet" href="https://fonts.googleapis.com/css2?family=Roboto:wght@400;500&family=Roboto+Condensed:wght@700&display=swap">
<style>
  :root {
    --backdrop: #e4e4e2;
    --card: #f6f6f5;
    --brand-blue: #1a8fc9;
    --deep-blue: #0e6f9c;
    --rule: #b9b9b9;
    --ink: #505050;
    --peach: #f8d6bd;
    --orange: #ef7a1f;
    --white: #ffffff;
  }
  * { margin: 0; padding: 0; box-sizing: border-box; }
  html, body { width: 1200px; height: 960px; overflow: hidden; }
  body {
    background: var(--backdrop);
    font-family: "Roboto", Arial, sans-serif;
    position: relative;
  }
  .business-card {
    position: absolute;
    left: 300px; top: 295px;
    width: 600px; height: 342px;
    background: var(--card);
    border-radius: 14px;
    overflow: hidden;
    box-shadow: 0 4px 14px rgba(0,0,0,0.18);
  }
  .brand-name {
    position: absolute;
    right: 30px; top: 58px;
    text-align: right;
    color: var(--brand-blue);
    font-weight: 500;
    line-height: 1;
  }
  .brand-name .brand-word { display: block; font-size: 50px; letter-spacing: -0.5px; }
  .brand-name .brand-tag { display: block; font-size: 15px; letter-spacing: 3px; margin-top: 10px; }
  .holder-name {
    position: absolute;
    left: 24px; top: 194px;
    font-family: "Roboto Condensed", "Arial Narrow", sans-serif;
    font-weight: 700;
    font-size: 21px;
    color: var(--brand-blue);
  }
  .divider {
    position: absolute;
    left: 25px; top: 229px;
    width: 544px; height: 1px;
    background: var(--rule);
  }
  .contact-list {
    position: absolute;
    left: 25px; top: 244px;
    list-style: none;
    font-size: 14px;
    color: var(--ink);
    line-height: 19px;
  }
  .contact-list li { display: flex; align-items: center; gap: 8px; }
  .contact-list svg { width: 14px; height: 14px; fill: var(--brand-blue); }
  .postal-address {
    position: absolute;
    right: 27px; top: 246px;
    text-align: right;
    font-size: 14px;
    font-style: normal;
    color: var(--ink);
    line-height: 19px;
  }
  .footer-band {
    position: absolute;
    left: 0; bottom: 0;
    width: 600px; height: 26px;
    background: linear-gradient(90deg, var(--peach) 0%, var(--orange) 55%, var(--deep-blue) 80%);
  }
  .web-address {
    position: absolute;
    right: 33px; bottom: 6px;
    font-size: 14px;
    color: var(--white);
  }
</style>
</head>
<body>
  <main class="business-card">
    <div class="brand-name">
      <span class="brand-word">Quorv</span>
      <span class="brand-tag">INTERNATIONAL</span>
    </div>

    <h1 class="holder-name">DENNIS MORVALE</h1>
    <div class="divider"></div>

    <ul class="contact-list">
      <li>
        <svg viewBox="0 0 24 24" aria-hidden="true"><path d="M6.6 10.8a15.1 15.1 0 0 0 6.6 6.6l2.2-2.2a1 1 0 0 1 1-.25 11.4 11.4 0 0 0 3.6.57 1 1 0 0 1 1 1V20a1 1 0 0 1-1 1A17 17 0 0 1 3 4a1 1 0 0 1 1-1h3.5a1 1 0 0 1 1 1c0 1.25.2 2.45.57 3.57a1 1 0 0 1-.25 1z"/></svg>
        +61 487215963
      </li>
      <li>
        <svg viewBox="0 0 24 24" aria-hidden="true"><path d="M2 5h20v14H2z M4 7v.5l8 5 8-5V7l-8 5z" fill-rule="evenodd"/></svg>
        dennis@quorv.com.au
      </li>
    </ul>

    <address class="postal-address">P.O. Box 872<br>Fernlow QLD 4309</address>

    <div class="footer-band" role="img" aria-label="Decorative footer band in peach, orange and blue"></div>
    <span class="web-address">www.quorv.com.au</span>
  </main>
</body>
</html>
```